Business Card - connecting 2 souls and beggining the journey of self discovery

Logo on the front
with tag line

On the back list of services and contact details

Seminars
workshops
Coaching
podcasts

Darren Whitlow
Health & Wellbeing Life Coach
0491 372 615
darren@brightcoreliving.example
brightcoreliving.example

Industry/Entity Type

Life Coaching

Contact Information for Business Card

I like the use of colour from the logo to be used. I'm not a fan of white.

Requirements
Must have
• My tagline: The journey home starts with you
Nice to have
• Use of colour that is in the Brightcore Living logo

```html
<!DOCTYPE html>
<html lang="en">
<head>
<meta charset="utf-8">
<title>Brightcore Living – Business Card</title>
<link href="https://fonts.googleapis.com/css2?family=Montserrat:wght@400;500;700&display=swap" rel="stylesheet">
<style>
  :root {
    --backdrop: #2a2a2a;
    --card-start: #f4ebf7;
    --card-mid: #fbf1ec;
    --card-end: #eef7f1;
    --purple: #8653a4;
    --purple-deep: #7a4b9a;
    --ink: #141414;
    --grey: #858085;
  }
  * { margin: 0; padding: 0; box-sizing: border-box; }
  html, body { width: 1200px; height: 1096px; overflow: hidden; }
  body {
    background: var(--backdrop);
    font-family: "Montserrat", Arial, sans-serif;
    position: relative;
  }
  .card {
    position: absolute;
    width: 550px;
    height: 317px;
    background: linear-gradient(135deg, var(--card-start) 0%, var(--card-mid) 55%, var(--card-end) 100%);
    overflow: hidden;
  }

  /* Services side */
  .card--services { left: 491px; top: 207px; }
  .band { position: absolute; left: 0; right: 0; background: var(--purple); }
  .band--top { top: 0; height: 11px; }
  .band--bottom { bottom: 0; height: 13px; background: var(--purple-deep); }

  .brand-mark {
    position: absolute;
    display: flex;
    align-items: center;
    gap: 8px;
    transform: translate(-50%, -50%);
    white-space: nowrap;
  }
  .brand-mark__dot {
    width: 16px; height: 16px; border-radius: 50%;
    background: var(--purple);
  }
  .brand-mark__name {
    font-weight: 700;
    font-size: 20px;
    color: var(--purple);
    letter-spacing: 0.2px;
  }
  .card--services .brand-mark { left: 275px; top: 112px; }

  .motto {
    position: absolute;
    left: 0; right: 0;
    text-align: center;
    font-weight: 500;
    font-size: 13px;
    color: var(--grey);
    letter-spacing: 0.3px;
  }
  .card--services .motto { top: 140px; }

  .services {
    position: absolute;
    left: 0; right: 0;
    top: 263px;
    display: flex;
    justify-content: center;
    gap: 14px;
    list-style: none;
  }
  .services li {
    display: flex;
    align-items: center;
    gap: 7px;
    font-weight: 700;
    font-size: 13px;
    color: var(--ink);
    letter-spacing: -0.1px;
  }
  .services li::before {
    content: "";
    width: 11px; height: 11px; border-radius: 50%;
    background: var(--purple);
  }

  /* Contact side */
  .card--contact { left: 197px; top: 566px; }
  .side-bar {
    position: absolute; left: 0; top: 0; bottom: 0; width: 39px;
    background: linear-gradient(180deg, #8d5aaa, #7b4b9c);
  }
  .tagline-tab {
    position: absolute; left: 19px; top: 24px;
    height: 48px; padding: 0 6px 0 4px;
    background: var(--card-start);
    display: flex; align-items: center;
  }
  .tagline {
    font-weight: 500;
    font-size: 34px;
    letter-spacing: -1.6px;
    color: var(--grey);
    white-space: nowrap;
  }
  .person { position: absolute; left: 44px; top: 196px; }
  .person__name, .person__role {
    font-weight: 700; font-size: 17px; color: var(--purple);
    line-height: 21px; letter-spacing: 0.1px;
  }
  .contact-list {
    position: absolute; left: 44px; top: 256px;
    list-style: none;
    font-size: 13px; line-height: 14.5px;
    color: var(--purple);
    font-weight: 500;
  }
  .card--contact .brand-mark { left: 436px; top: 207px; gap: 7px; }
  .card--contact .brand-mark__dot { width: 14px; height: 14px; }
  .card--contact .brand-mark__name { font-size: 18px; }
</style>
</head>
<body>

<section class="card card--services">
  <div class="band band--top"></div>
  <div class="brand-mark">
    <span class="brand-mark__dot"></span>
    <span class="brand-mark__name">Brightcore Living</span>
  </div>
  <p class="motto">The journey home starts with you</p>
  <ul class="services">
    <li>SEMINAR</li>
    <li>WORKSHOP</li>
    <li>COACHING</li>
    <li>PODCAST</li>
  </ul>
  <div class="band band--bottom"></div>
</section>

<section class="card card--contact">
  <div class="side-bar"></div>
  <div class="tagline-tab"><span class="tagline">Home of Brightcore Living</span></div>
  <div class="person">
    <p class="person__name">Darren Whitlow</p>
    <p class="person__role">Health &amp; Wellbeing Life Coach</p>
  </div>
  <ul class="contact-list">
    <li>T&nbsp; : &nbsp;0491 372 615</li>
    <li>E&nbsp; : darren@brightcoreliving.example</li>
    <li>W : brightcoreliving.example</li>
  </ul>
  <div class="brand-mark">
    <span class="brand-mark__dot"></span>
    <span class="brand-mark__name">Brightcore Living</span>
  </div>
</section>

</body>
</html>
```